Boutique custom software development company needs new business card

Our nearly 20 year old custom software development company would like to better include the fact that we are now providing Bitcoin services. These new services are B2B include education (how to acquire and securely hold Bitcoin) and integrating Bitcoin payments into existing ecommerce sites or other existing systems. Please keep the card clean and simple. Attached is our current design and some other files. vextorial.com

Target Market(s)

businesses owners interested in long term relationship

Industry/Entity Type

Custom software development and Bitcoin

Contact Information for Business Card

Dale Parker, dale@vextorial.com, vextorial.com, (888) 555-VXTRL

Font styles to use
Other font styles liked:
• monospace

Requirements
Must have
• double-sided
Nice to have
• clean and simple
Should not have
• physical address

```html
<!DOCTYPE html>
<html lang="en">
<head>
<meta charset="utf-8">
<title>Vextorial business card</title>
<link rel="stylesheet" href="https://fonts.googleapis.com/css2?family=Montserrat:wght@400;500;600;700&display=swap">
<style>
  :root {
    --page: #ece8e2;
    --card-white: #ffffff;
    --brand-blue: #3f73bb;
    --brand-blue-light: #8fb0dc;
    --brand-blue-dark: #2d5a99;
    --ink: #3a3a3a;
    --muted: #4a4a4a;
  }
  * { box-sizing: border-box; margin: 0; padding: 0; }
  html, body { width: 900px; height: 1200px; overflow: hidden; }
  body {
    background: var(--page);
    font-family: "Montserrat", sans-serif;
    position: relative;
  }
  .card {
    position: absolute;
    left: 80px;
    width: 742px;
    height: 440px;
    border-radius: 40px;
    overflow: hidden;
    box-shadow: 0 4px 10px rgba(0,0,0,0.25);
  }
  .card--front { top: 132px; background: var(--card-white); }
  .card--back { top: 638px; background: var(--brand-blue); }

  .brand-block {
    position: absolute;
    left: 138px;
    top: 150px;
    width: 166px;
    height: 166px;
    display: flex;
    flex-direction: column;
    align-items: center;
    justify-content: center;
    gap: 14px;
  }
  .brand-square { width: 70px; height: 70px; background: var(--brand-blue); }
  .brand-name {
    font-weight: 700;
    font-size: 24px;
    letter-spacing: 1px;
    color: var(--brand-blue);
  }
  .divider {
    position: absolute;
    left: 360px;
    top: 143px;
    width: 2px;
    height: 176px;
    background: var(--brand-blue);
  }
  .details { position: absolute; left: 413px; top: 155px; }
  .person-name { font-weight: 700; font-size: 26px; color: var(--brand-blue); line-height: 1.1; }
  .person-role { font-size: 15px; color: var(--muted); margin-top: 2px; }
  .contact-list { list-style: none; margin-top: 28px; }
  .contact-list li {
    display: flex;
    align-items: center;
    gap: 9px;
    font-size: 16px;
    color: var(--ink);
    height: 22.5px;
  }
  .contact-list svg { width: 14px; height: 14px; fill: var(--brand-blue); flex: none; }

  .pattern-field {
    position: absolute;
    inset: 0;
    background: linear-gradient(90deg, #a9c3e6 0%, #7a9fd3 40%, #4f7dc0 70%, #2f5c9c 100%);
    opacity: 0.55;
  }
  .wordmark {
    position: absolute;
    left: 286px;
    top: 280px;
    display: flex;
    align-items: flex-start;
    gap: 14px;
  }
  .wordmark-square { width: 69px; height: 67px; background: var(--card-white); }
  .wordmark-text { color: var(--card-white); }
  .wordmark-name { font-weight: 700; font-size: 44px; line-height: 46px; letter-spacing: 0.5px; }
  .wordmark-tagline { font-weight: 500; font-size: 16px; margin-top: 6px; white-space: nowrap; }
</style>
</head>
<body>
  <section class="card card--front">
    <div class="brand-block">
      <div class="brand-square"></div>
      <div class="brand-name">VEXTORIAL</div>
    </div>
    <div class="divider"></div>
    <div class="details">
      <div class="person-name">Dale Parker</div>
      <div class="person-role">Owner</div>
      <ul class="contact-list">
        <li>
          <svg viewBox="0 0 16 16"><path d="M2 6c0-2 2-3 6-3s6 1 6 3v1h-3V5.5H5V7H2zM4 8h8l2 5H2z"/></svg>
          (888) 555-VXTRL
        </li>
        <li>
          <svg viewBox="0 0 16 16"><path d="M1 3h14v1L8 9 1 4zM1 5.5l7 5 7-5V13H1z"/></svg>
          dale@vextorial.com
        </li>
        <li>
          <svg viewBox="0 0 16 16"><circle cx="8" cy="8" r="7"/></svg>
          www.vextorial.com
        </li>
      </ul>
    </div>
  </section>

  <section class="card card--back">
    <div class="pattern-field" role="img" aria-label="Repeating tiled brand pattern fading from light to dark blue"></div>
    <div class="wordmark">
      <div class="wordmark-square"></div>
      <div class="wordmark-text">
        <div class="wordmark-name">VEXTORIAL</div>
        <div class="wordmark-tagline">custom software &amp; Bitcoin services</div>
      </div>
    </div>
  </section>
</body>
</html>
```